International non-profit org needs web design

A new non-profit global organization called The Global Venture Bridge Council (GVBC) needs a web design. The organization is a global community of professionals engaged in the commercialization aspects of innovation. The members of the community share experience and knowledge about exemplary practices and business models in order to continuoulsy improve the field of expertise.

Target Market(s)

governments, investors, universities, professionala

Industry/Entity Type

Non-Profit

Requirements
Must have
• landing page and capability to add tabs

```html
<!DOCTYPE html>
<html lang="en">
<head>
<meta charset="utf-8">
<title>GVBC – The Global Venture Bridge Council</title>
<link href="https://fonts.googleapis.com/css2?family=Arimo:wght@400;700&family=Noto+Sans:wght@400;700&family=Roboto+Condensed:wght@400;700&display=swap" rel="stylesheet">
<style>
:root{
  --red:#d4202b;
  --red-dark:#8c0d14;
  --ink:#1a1a1a;
  --panel:#1c1c1c;
  --band:#2a2a2a;
  --grey-text:#555;
  --soft-grey:#f2f2f2;
  --input:#555759;
  --foot:#2c2c2c;
  --foot-line:#3d3d3d;
  --foot-text:#d8d8d8;
  --foot-muted:#8d8d8d;
}
*{margin:0;padding:0;box-sizing:border-box}
html,body{width:1144px;height:1200px;overflow:hidden;background:#fff}
body{position:relative;font-family:"Arimo",Arial,sans-serif;color:var(--ink)}
.abs{position:absolute}

/* header */
.site-header{position:absolute;left:0;top:0;width:1144px;height:107px;background:#fff}
.brand{position:absolute;left:176px;top:14px;height:73px;display:flex;align-items:center}
.brand-dot{width:54px;height:54px;border-radius:50%;background:var(--red);margin-right:12px}
.brand-name{font-family:"Arimo",sans-serif;font-weight:700;font-size:60px;color:var(--red);letter-spacing:1px;line-height:1}
.brand-rule{width:2px;height:73px;background:#333;margin:0 10px 0 14px}
.brand-tagline{font-family:"Roboto Condensed",sans-serif;font-weight:700;font-size:15px;line-height:18px;letter-spacing:1.4px;color:#222}
.search{position:absolute;left:793px;top:23px;width:161px;height:27px;background:#3a3a3a;border-radius:4px}
.search svg{position:absolute;right:6px;top:3px}
.phone{position:absolute;left:784px;top:62px;display:flex;align-items:center}
.phone-icon{width:24px;height:25px;background:var(--red-dark);border-radius:4px;display:flex;align-items:center;justify-content:center}
.phone-number{margin-left:16px;font-size:20px;color:#222}

/* navigation */
.nav-band{position:absolute;left:0;top:107px;width:1144px;height:51px;background:linear-gradient(#3a3a3a,#1e1e1e);border-bottom:2px solid #111}
.main-nav{position:absolute;left:181px;top:112px;width:784px;height:44px;background:linear-gradient(#e03a42,#b5161f 55%,#3a1a1c);border-radius:3px}
.nav-item{position:absolute;top:10px;font-family:"Noto Sans",sans-serif;font-size:12px;color:#fff;transform:translateX(-50%);white-space:nowrap}
.nav-active{position:absolute;left:12px;top:2px;width:66px;height:34px;background:#4a4a4a;border-radius:3px}
.nav-divider{position:absolute;top:0;width:1px;height:44px;background:rgba(80,0,0,.55);box-shadow:1px 0 rgba(255,255,255,.15)}

/* hero */
.hero-band{position:absolute;left:0;top:158px;width:1144px;height:302px;background:var(--soft-grey);border-bottom:1px solid #ddd}
.hero{position:absolute;left:180px;top:170px;width:786px;height:279px;border:1px solid #bbb;border-radius:3px;overflow:hidden;
  background:linear-gradient(90deg,#f4f5f6 0%,#e6ebef 35%,#cfdbe6 55%,#8da3bd 75%,#c8d4e0 92%,#eef0f2 100%)}
.hero-caption{position:absolute;left:180px;top:265px;width:341px;height:89px;background:linear-gradient(#1f1f1f,#050505);border-radius:0 3px 3px 0;color:#fff;padding:21px 0 0 35px;font-family:"Noto Sans",sans-serif}
.hero-caption .small{font-size:14px;line-height:17px}
.hero-caption .big{font-size:23px;line-height:27px}
.hero-dot{position:absolute;top:419px;width:18px;height:18px;border-radius:50%;background:#1b1b1b}
.hero-dot.active{background:var(--red)}

/* sidebar */
.box{position:absolute;left:188px;width:220px;border-radius:3px;background:var(--panel);overflow:hidden}
.box-title{height:38px;padding:10px 0 0 22px;font-size:16px;color:#fff;background:linear-gradient(#2c2c2c,#141414)}
.box-red{background:linear-gradient(#c21d26,#7d0b11)}
.field{position:absolute;background:var(--input)}
.btn-light{position:absolute;background:linear-gradient(#fff,#e4e4e4);border-radius:4px;font-size:11px;color:#111;text-align:center;line-height:26px}
.login-label{position:absolute;left:17px;font-size:10px;color:#3a0305}
.news-title{position:absolute;left:4px;top:4px;width:211px;height:39px;background:linear-gradient(#d8262f,#a5121a);padding:12px 0 0 18px;font-size:16px;color:#fff}
.news-date{position:absolute;left:4px;width:61px;height:19px;background:#b3151e;font-size:9px;color:#fff;line-height:19px;text-align:center}
.news-text{position:absolute;left:67px;width:148px;font-size:10px;line-height:14.7px;color:#d4d4d4}
.news-more{display:block;color:var(--red)}

/* main content */
.welcome-title{position:absolute;left:448px;top:486px;font-family:"Noto Sans",sans-serif;font-size:15px;color:#111}
.welcome-title span{color:var(--red);font-size:18px}
.welcome-text{position:absolute;left:450px;top:519px;width:480px;font-family:"Noto Sans",sans-serif;font-size:12.6px;line-height:19.6px;color:var(--grey-text)}
.feature-title{position:absolute;top:680px;font-family:"Noto Sans",sans-serif;font-size:14px;color:#111;transform:translateX(-50%);white-space:nowrap}
.feature-title span{color:var(--red)}
.feature-art{position:absolute;border-radius:8px}
.feature-text{position:absolute;top:871px;width:192px;font-size:10.4px;line-height:16.3px;color:#333}
.btn-red{position:absolute;top:968px;width:97px;height:25px;border-radius:3px;background:linear-gradient(#c4222b,#7e0c12);color:#fff;font-size:11px;text-align:center;line-height:25px}
.col-divider{position:absolute;left:689px;top:683px;height:268px;border-left:1px dotted #999}

/* footer */
.site-footer{position:absolute;left:0;top:1041px;width:1144px;height:159px;background:var(--foot);border-top:2px solid #111}
.foot-divider{position:absolute;top:0;width:1px;height:155px;background:var(--foot-line)}
.foot-title{position:absolute;top:10px;font-size:15.5px;color:#fff;letter-spacing:.3px}
.foot-contact{position:absolute;left:204px;top:38px;font-family:"Noto Sans",sans-serif;font-size:11.8px;line-height:16.4px;color:var(--foot-text)}
.foot-note{position:absolute;left:478px;width:200px;font-size:10px;line-height:16.4px;color:var(--foot-muted)}
.foot-more{position:absolute;left:484px;top:127px;font-size:10px;color:var(--red)}
.social{position:absolute;top:50px;width:21px;height:21px;border-radius:50%}
.foot-links{position:absolute;left:710px;top:92px;font-size:10px;color:#ccc;word-spacing:1px}
.foot-links i{font-style:normal;margin:0 12px}
.copyright{position:absolute;left:749px;top:118px;font-size:10px;color:#ccc}
</style>
</head>
<body>

<header class="site-header">
  <div class="brand">
    <div class="brand-dot"></div>
    <div class="brand-name">GVBC</div>
    <div class="brand-rule"></div>
    <div class="brand-tagline">GLOBAL VENTURE<br>BRIDGE<br>COUNCIL</div>
  </div>
  <div class="search">
    <svg width="22" height="22" viewBox="0 0 22 22" aria-hidden="true"><circle cx="9" cy="9" r="6" fill="none" stroke="#ddd" stroke-width="2"/><line x1="13.5" y1="13.5" x2="20" y2="20" stroke="#ddd" stroke-width="3" stroke-linecap="round"/></svg>
  </div>
  <div class="phone">
    <div class="phone-icon"><svg width="14" height="16" viewBox="0 0 14 16" aria-hidden="true"><path d="M3 1h3l1 4-2 1c1 2 2 4 4 5l1-2 4 1v3c0 1-1 2-2 2C6 15 1 9 1 3c0-1 1-2 2-2z" fill="#fff"/></svg></div>
    <div class="phone-number">555-014-2290</div>
  </div>
</header>

<div class="nav-band"></div>
<nav class="main-nav">
  <div class="nav-active"></div>
  <span class="nav-item" style="left:48px">Home</span>
  <span class="nav-item" style="left:127px">About Us</span>
  <span class="nav-item" style="left:205px">Ideas</span>
  <span class="nav-item" style="left:297px">Announcement</span>
  <span class="nav-item" style="left:408px">What We Do</span>
  <span class="nav-item" style="left:508px">Our Profile</span>
  <span class="nav-item" style="left:605px">Contact Us</span>
  <span class="nav-item" style="left:694px">Register</span>
  <div class="nav-divider" style="left:80px"></div>
  <div class="nav-divider" style="left:169px"></div>
  <div class="nav-divider" style="left:235px"></div>
  <div class="nav-divider" style="left:354px"></div>
  <div class="nav-divider" style="left:459px"></div>
  <div class="nav-divider" style="left:552px"></div>
  <div class="nav-divider" style="left:651px"></div>
</nav>

<div class="hero-band"></div>
<div class="hero" role="img" aria-label="Photo of a smiling businessman with folded arms in a bright office with tall windows"></div>
<div class="hero-caption"><div class="small">Need Advice for your</div><div class="big">Business Development?</div></div>
<span class="hero-dot active" style="left:249px"></span>
<span class="hero-dot" style="left:269px"></span>
<span class="hero-dot" style="left:289px"></span>
<span class="hero-dot" style="left:309px"></span>

<aside>
  <section class="box" style="top:479px;height:154px">
    <div class="box-title">NEWSLETTER</div>
    <div class="box-red abs" style="left:0;top:38px;width:220px;height:97px"></div>
    <div class="field" style="left:20px;top:56px;width:137px;height:28px"></div>
    <div class="btn-light" style="left:52px;top:101px;width:78px;height:26px">SUBSCRIBE</div>
  </section>

  <section class="box" style="top:644px;height:178px">
    <div class="box-title">LOGIN</div>
    <div class="box-red abs" style="left:0;top:38px;width:220px;height:122px"></div>
    <div class="login-label" style="top:56px">USER NAME &nbsp;&nbsp;:</div>
    <div class="field" style="left:91px;top:52px;width:116px;height:23px"></div>
    <div class="login-label" style="top:98px">PASSWORD &nbsp;&nbsp;&nbsp;:</div>
    <div class="field" style="left:91px;top:94px;width:116px;height:23px"></div>
    <div class="btn-light" style="left:98px;top:126px;width:78px;height:26px">SUBMIT</div>
  </section>

  <section class="box" style="top:832px;height:203px;background:linear-gradient(#2a2a2a,#050505)">
    <div class="news-title">LATEST NEWS</div>
    <div class="news-date" style="top:57px">OCT 12, 2011</div>
    <p class="news-text" style="top:53px">Lum mlecnean maurilra kerase meras soc totisenonlu sermerse ase lertaslrurbi nuodgravida.<span class="news-more">more</span></p>
    <div class="news-date" style="top:139px">OCT 12, 2011</div>
    <p class="news-text" style="top:135px">Lum mlecnean maurilra kerase meras soc totisenonlu sermerse ase lertaslrurbi nuodgravida.<span class="news-more">more</span></p>
  </section>
</aside>

<main>
  <h1 class="welcome-title">WELCOME TO <span>GVBC</span></h1>
  <p class="welcome-text">Lorem ipsum dolor sit amet, adipiscing elit. Nam nibh. Nunc varius facilisis eros. Sed erat.In in velit quis arcuornare laoreet. Curabitur adipiscing luctus massa. Integer ut purus ac commodo commodo.<br>Lorem ipsum dolor sit amet, adipiscing elit. Nam nibh. Nunc varius facilisis eros. Sed erat.In in velit quis arcuornare laoreet. Curabitur adipiscing luctus massa. Integer ut purus ac commodo commodo.</p>

  <h2 class="feature-title" style="left:544px">WHAT <span>WE DO</span></h2>
  <div class="feature-art" style="left:476px;top:707px;width:130px;height:156px;background:radial-gradient(ellipse at 50% 40%,#3a8ee0,#a9c9ea 60%,#fff 80%)" role="img" aria-label="Illustration of two blue figures shaking hands on puzzle pieces"></div>
  <p class="feature-text" style="left:458px">Lorem ipsum dolor sit amet, consectetuer adipiscing elit. Nam nibh. Nunc varius facilisis eros. Sed erat. Lorem ipsum dolor sit amet, consectetuer adipiscing elit. Nam nibh. Nunc varius facilisis eros. Sed erat.</p>
  <div class="btn-red" style="left:501px">Read more</div>

  <div class="col-divider"></div>

  <h2 class="feature-title" style="left:823px">WHO <span>WE ARE</span></h2>
  <div class="feature-art" style="left:784px;top:732px;width:94px;height:106px;background:radial-gradient(ellipse at 50% 45%,#5a5a5a,#9a9a9a 60%,#fff 78%)" role="img" aria-label="Icon of a businessman in a dark suit"></div>
  <p class="feature-text" style="left:737px">Lorem ipsum dolor sit amet, consectetuer adipiscing elit. Nam nibh. Nunc varius facilisis eros. Sed erat. Lorem ipsum dolor sit amet, consectetuer adipiscing elit. Nam nibh. Nunc varius facilisis eros. Sed erat.</p>
  <div class="btn-red" style="left:788px">Read more</div>
</main>

<footer class="site-footer">
  <div class="foot-divider" style="left:429px"></div>
  <div class="foot-divider" style="left:691px"></div>

  <h3 class="foot-title" style="left:202px">CONTACT US</h3>
  <address class="foot-contact" style="font-style:normal">Dr. Elena Varga<br>The Crossline Policy Forum<br>Northbridge Trade Office<br>Westhaven,<br><br>Email &nbsp;:elena.varga@gvbc-network.org</address>

  <h3 class="foot-title" style="left:480px">ANNOUNCEMENTS</h3>
  <p class="foot-note" style="top:42px">Lorem ipsum dolor sit amet, consectetuer adipiscing elit. Nam nibh. Nunc varius</p>
  <p class="foot-note" style="top:84px">Lorem ipsum dolor sit amet, consectetuer adipiscing elit. Nam nibh. Nunc varius</p>
  <span class="foot-more">more</span>

  <h3 class="foot-title" style="left:742px">CONNECT US</h3>
  <span class="social" style="left:809px;background:#2a5aa8"></span>
  <span class="social" style="left:841px;background:#3ba7dc"></span>
  <span class="social" style="left:874px;background:#1f79b5"></span>
  <span class="social" style="left:905px;background:#e8731f"></span>
  <div class="foot-links">Privacy Policy<i>|</i>Terms &amp; Conditions<i>|</i>Contact Us</div>
  <div class="copyright">Copyright © GVBC, All Rights Reserved</div>
</footer>

</body>
</html>
```